Business cards for Norwegian software consultancy business

We are in need of business cards for our Norwegian consultancy company.
“Valto Brindex AS” specializes in software development, architecture and agile methodology, providing mostly on-site services at customers.
The cards should reflect a certain level of business professionalism with an elegant touch, while paying tribute to our modern and technological heritage. Our logo should be featured, as well as room for basic information about the cardholder and legal information of the company (company name, address and VAT number).
We would like our cards to reflect that we are a modern consulting company. It should present a professional image that people will remember. The texture and color pallette should reflect our professionalism and reliability, so we prefer a light color pallette with colors such as gray, white, blue and black. The number of colors used should however not be overwhelming, with the text being distinct and readable.
We are open to untraditional layouts and playful designs as long as they communicate the intent stated above.
You could also take a look at our website http://www.brindex.no for input on our visual profile.
Our logo is attached in the form of vectors and rasterized PNG. Please comment if you would like the black-white and/or inverted versions as well.
Industry/Entity Type
Architecture
Contact Information for Business Card
Company information:
Valto Brindex AS
Kvernlia 14, 3170 Sem
482 71 519
info@brindex.no
www.brindex.no
Employee information:
Full name
Title
Email
Phone
Font styles to use
Look and feel

```html
<!DOCTYPE html>
<html lang="no">
<head>
<meta charset="utf-8">
<title>Valto Brindex AS – Business Card</title>
<link rel="stylesheet" href="https://fonts.googleapis.com/css2?family=Lato:wght@300;400;700&display=swap">
<style>
  :root {
    --backdrop: #d9dadb;
    --card-white: #fbfbfb;
    --panel-dark: #3a3b3d;
    --accent-blue: #6b9fcd;
    --ink-dark: #3b3c3e;
    --ink-light: #f2f2f2;
    --ink-muted: #d6d7d8;
  }
  * { box-sizing: border-box; margin: 0; padding: 0; }
  html, body {
    width: 1200px;
    height: 900px;
    overflow: hidden;
    background: var(--backdrop);
    font-family: "Lato", Arial, sans-serif;
  }
  .canvas {
    position: relative;
    width: 1200px;
    height: 900px;
  }
  .business-card {
    position: absolute;
    left: 150px;
    top: 193px;
    width: 900px;
    height: 514px;
    background: var(--card-white);
    box-shadow: 0 10px 30px rgba(0, 0, 0, 0.18);
    overflow: hidden;
  }
  .brand {
    position: absolute;
    left: 70px;
    top: 176px;
    display: flex;
    align-items: center;
    gap: 16px;
  }
  .brand-square {
    width: 30px;
    height: 30px;
    background: var(--accent-blue);
  }
  .brand-name {
    font-size: 40px;
    font-weight: 300;
    letter-spacing: 1px;
    color: var(--ink-dark);
  }
  .website {
    position: absolute;
    left: 70px;
    bottom: 78px;
    font-size: 19px;
    font-weight: 400;
    letter-spacing: 5px;
    color: var(--ink-dark);
  }
  .info-panel {
    position: absolute;
    left: 440px;
    top: 22px;
    right: 0;
    height: 398px;
    background: var(--panel-dark);
    color: var(--ink-light);
    padding: 56px 40px 0 74px;
  }
  .holder {
    position: relative;
  }
  .holder-marker {
    position: absolute;
    left: -40px;
    top: 30px;
    width: 0;
    height: 0;
    border-top: 9px solid transparent;
    border-bottom: 9px solid transparent;
    border-left: 15px solid var(--accent-blue);
  }
  .holder-name {
    font-size: 32px;
    font-weight: 400;
    line-height: 1.1;
  }
  .holder-title {
    font-size: 17px;
    font-weight: 400;
    letter-spacing: 1px;
    color: var(--ink-muted);
    margin-top: 4px;
  }
  .company-address {
    margin-top: 30px;
    font-size: 21px;
    line-height: 1.3;
    font-style: normal;
  }
  .company-name {
    font-weight: 700;
  }
  .contact-list {
    list-style: none;
    margin-top: 30px;
    font-size: 21px;
    line-height: 1.3;
  }
  .contact-list li {
    display: flex;
    align-items: center;
    gap: 16px;
  }
  .contact-icon {
    width: 18px;
    height: 18px;
    flex: none;
    fill: none;
    stroke: var(--accent-blue);
    stroke-width: 1.6;
  }
</style>
</head>
<body>
<div class="canvas">
  <article class="business-card">
    <div class="brand">
      <span class="brand-square"></span>
      <span class="brand-name">Valto Brindex</span>
    </div>
    <p class="website">www.brindex.no</p>

    <section class="info-panel">
      <div class="holder">
        <span class="holder-marker"></span>
        <h1 class="holder-name">Eirik Dalen</h1>
        <p class="holder-title">DIRECTOR</p>
      </div>
      <address class="company-address">
        <span class="company-name">Valto Brindex AS</span><br>
        Kvernlia 14<br>
        3170 Sem
      </address>
      <ul class="contact-list">
        <li>
          <svg class="contact-icon" viewBox="0 0 18 18" aria-hidden="true"><path d="M4 2 L7 2 L8 6 L6 7.5 C7 10 8 11 10.5 12 L12 10 L16 11 L16 14 C16 15 15 16 14 16 C8 16 2 10 2 4 C2 3 3 2 4 2 Z"/></svg>
          <span>482 71 519</span>
        </li>
        <li>
          <svg class="contact-icon" viewBox="0 0 18 18" aria-hidden="true"><rect x="5" y="2" width="8" height="5"/><rect x="2" y="7" width="14" height="6"/><rect x="5" y="11" width="8" height="5"/></svg>
          <span>482 71 520</span>
        </li>
        <li>
          <svg class="contact-icon" viewBox="0 0 18 18" aria-hidden="true"><rect x="2" y="4" width="14" height="10"/><path d="M2 4 L9 10 L16 4"/></svg>
          <span>edalen@brindex.no</span>
        </li>
      </ul>
    </section>
  </article>
</div>
</body>
</html>
```